Upstart Retirement Planning Firm needs help with business card design

Harborview Nest Advisors, LLC is looking for help with business card design. We give advice on investments, insurance, and other financial matters related to retirement. There are some required disclosures that we will provide but mostly we are looking for a professional, classy business card that reflects the theme we have chosen. We have a logo that is attached but we would like to add a phrase; "Shaping Your Working Years Into Lasting Security"

Doubled sided only so that we can add the required disclosures (needed for our industry) on the back of the card. We will provide the exact words for this in 1-2 days.

Target Market(s)

Retirees and Pre-retirees. Professionals 50+ years old

Industry/Entity Type

Financial Planning

Contact Information for Business Card

We currently have two people who will need separate cards so we'd like to have a template so that we can add names for new cards in the future.

For the first run, please show the following information.

Gregor Pelham, MBA, ChFC®, CLU®
Financial Advisor, Registered Representative
gpelham@harborviewnest.example
Phone: (555) 318-2946
Toll Free Fax: (800) 555-0193

Address is
2187 Meadowlark Ridge Rd.
Suite K418
Virginia Beach, VA 23999

Colors
3277b5

Requirements
Must have
• Logo, contact info, small phase to describe business (in description), required legal disclosures on back of the card as follows (in small font)
• Gregor Pelham is a registered representative of and offers securities through Brightmoor Capital Brokerage Corporation, Member FNQX. Brightmoor Capital Brokerage Corporation is a member of the Brightmoor Capital Alliance which is the marketing name for Brightmoor Holding Corporation and its affiliates.
Nice to have
• Rounded edges, raised letters
Should not have
• any colors that aren't in the logo (other than black for font)

```html
<!DOCTYPE html>
<html lang="en">
<head>
<meta charset="utf-8">
<title>Harborview Nest Advisors – Business Cards</title>
<link rel="stylesheet" href="https://fonts.googleapis.com/css2?family=Open+Sans:wght@400;600&display=swap">
<style>
  :root {
    --backdrop: #3a332f;
    --card: #0c0c0d;
    --card-edge: #1c1c1e;
    --brand-blue: #3277b5;
    --silver: #c9cacc;
    --text: #e6e6e6;
    --rule: #5a5b5e;
  }
  * { box-sizing: border-box; margin: 0; padding: 0; }
  html, body { width: 1200px; height: 900px; overflow: hidden; }
  body {
    background: var(--backdrop);
    font-family: "Open Sans", Arial, sans-serif;
    position: relative;
  }
  .card {
    position: absolute;
    top: 301px;
    width: 525px;
    height: 298px;
    background: var(--card);
    border: 1px solid var(--card-edge);
    border-radius: 10px;
    box-shadow: 0 10px 30px rgba(0,0,0,.45);
    color: var(--text);
  }
  .card--info { left: 45px; }
  .card--brand { left: 630px; }

  /* info side */
  .brand-block {
    position: absolute;
    left: 24px;
    top: 150px;
    width: 222px;
    text-align: center;
  }
  .brand-name {
    font-size: 12.5px;
    font-weight: 400;
    color: var(--silver);
    letter-spacing: .02em;
    line-height: 1.35;
    white-space: nowrap;
  }
  .brand-rule {
    height: 1px;
    background: var(--rule);
    margin: 8px 10px 0;
  }
  .divider {
    position: absolute;
    left: 256px;
    top: 30px;
    width: 1px;
    height: 180px;
    background: #232428;
  }
  .contact {
    position: absolute;
    left: 276px;
    top: 30px;
    font-size: 12.5px;
    line-height: 1.45;
  }
  .person-name {
    color: var(--brand-blue);
    font-size: 15px;
    font-weight: 600;
  }
  .credentials { font-size: 9px; font-weight: 600; }
  .role { margin-bottom: 14px; }
  .address { margin-bottom: 14px; }
  .line { display: flex; align-items: center; gap: 6px; }
  .line svg { flex: none; }

  /* brand side */
  .brand-center {
    position: absolute;
    left: 0; right: 0;
    top: 102px;
    text-align: center;
  }
  .brand-center .brand-name { font-size: 21px; letter-spacing: .04em; }
  .brand-center .brand-rule { width: 280px; margin: 12px auto 0; }
  .tagline {
    margin-top: 16px;
    font-size: 12.5px;
    color: var(--silver);
    letter-spacing: .02em;
  }
</style>
</head>
<body>

  <section class="card card--info" aria-label="Business card, contact side">
    <div class="brand-block">
      <p class="brand-name">Harborview Nest Advisors, LLC</p>
      <div class="brand-rule"></div>
    </div>

    <div class="divider"></div>

    <div class="contact">
      <p class="person-name">Gregor Pelham, <span class="credentials">MBA, ChFC®, CLU®</span></p>
      <p class="role">Financial Advisor<br>Registered Representative</p>
      <p class="address">2187 Meadowlark Ridge Rd.<br>Suite K418<br>Virginia Beach, VA 23999</p>
      <p class="line">
        <svg width="11" height="11" viewBox="0 0 24 24" aria-hidden="true"><path fill="#3277b5" d="M6.6 10.8a15 15 0 0 0 6.6 6.6l2.2-2.2c.3-.3.7-.4 1-.2 1.1.4 2.3.6 3.6.6.6 0 1 .4 1 1V20c0 .6-.4 1-1 1A17 17 0 0 1 3 4c0-.6.4-1 1-1h3.5c.6 0 1 .4 1 1 0 1.3.2 2.5.6 3.6.1.3 0 .7-.2 1z"/></svg>
        (555) 318-2946
      </p>
      <p class="line">
        <svg width="11" height="11" viewBox="0 0 24 24" aria-hidden="true"><rect x="2" y="5" width="20" height="14" rx="2" fill="#3277b5"/><path d="M3 6l9 7 9-7" stroke="#0c0c0d" stroke-width="1.6" fill="none"/></svg>
        gpelham@harborviewnest.example
      </p>
      <p>Toll Free Fax: (800) 555-0193</p>
    </div>
  </section>

  <section class="card card--brand" aria-label="Business card, brand side">
    <div class="brand-center">
      <p class="brand-name">Harborview Nest Advisors, LLC</p>
      <div class="brand-rule"></div>
      <p class="tagline">Shaping Your Working Years Into Lasting Security</p>
    </div>
  </section>

</body>
</html>
```